Kelvor Engineers: Why you should hire us keepsake

New design. Open to plastic cards. We are an engineering firm that designs cell phone towers and commercial buildings. Please check out our website www.kelvorstruct.com for more details. We want people to remember our card and for it to be useful if possible. We want the same look and feel on these cards to be translated to other marketing material we may need such as brochures.

Target Market(s)

Architects, Developers and Telecommunication Carriers

Industry/Entity Type

Engineering

Contact Information for Business Card

Card with our company colors, logo, and innovative design with elements related to our industry.

Font styles to use
Sans Serif

Colors
9bcb3c
abd036
0255a3

Requirements
Must have
• Sleek and hip design
Nice to have
• Bright lime green and navy coloring that pops with an innovative design.
Should not have
• A basic and boring design

```html
<!DOCTYPE html>
<html lang="en">
<head>
<meta charset="utf-8">
<title>Kelvor Engineers – Business Card</title>
<link rel="stylesheet" href="https://fonts.googleapis.com/css2?family=Roboto:wght@400;500;700;900&display=swap">
<style>
  :root {
    --lime: #cdd52b;
    --lime-deep: #b9c424;
    --navy: #1c356b;
    --white: #ffffff;
    --backdrop: #2a2a2c;
  }
  * { box-sizing: border-box; margin: 0; padding: 0; }
  html, body { width: 1200px; height: 930px; overflow: hidden; }
  body {
    background: var(--backdrop);
    font-family: "Roboto", Arial, sans-serif;
    display: flex;
    align-items: center;
    justify-content: center;
    gap: 40px;
  }
  .card {
    position: relative;
    width: 540px;
    height: 309px;
    border-radius: 18px;
    overflow: hidden;
    box-shadow: 0 10px 30px rgba(0,0,0,0.45);
  }
  /* Front */
  .card-front { background: var(--lime); }
  .front-name {
    position: absolute;
    left: 0; right: 0; top: 100px;
    text-align: center;
    font-size: 54px;
    font-weight: 900;
    color: var(--white);
    letter-spacing: -1px;
    line-height: 1;
  }
  .front-cities {
    position: absolute;
    left: 0; right: 0; bottom: 34px;
    text-align: center;
    font-size: 15px;
    font-weight: 500;
    color: var(--white);
    letter-spacing: 1.5px;
    text-transform: uppercase;
  }
  .front-cities .sep { margin: 0 8px; }
  /* Back */
  .card-back { background: var(--white); }
  .back-shapes { position: absolute; inset: 0; }
  .person {
    position: absolute;
    right: 30px; top: 16px;
    text-align: right;
  }
  .person-name { font-size: 19px; font-weight: 700; color: var(--navy); }
  .person-title { font-size: 12px; color: var(--white); margin-top: 1px; }
  .back-name {
    position: absolute;
    left: 40px; top: 170px;
    font-size: 40px;
    font-weight: 900;
    color: var(--lime);
    letter-spacing: -1px;
    line-height: 1;
  }
  .tagline {
    position: absolute;
    left: 290px; top: 116px;
    font-size: 13px;
    font-weight: 500;
    color: var(--navy);
    letter-spacing: 1px;
    text-transform: uppercase;
  }
  .contacts {
    position: absolute;
    right: 22px; top: 196px;
    list-style: none;
    font-size: 13px;
    color: var(--white);
  }
  .contacts li {
    display: flex;
    justify-content: flex-end;
    align-items: center;
    gap: 8px;
    line-height: 18px;
  }
  .contacts svg { width: 10px; height: 10px; fill: var(--lime); flex: none; }
</style>
</head>
<body>

  <section class="card card-front" aria-label="Card front">
    <div class="front-name">Kelvor Engineers</div>
    <p class="front-cities">Atlanta<span class="sep">|</span>Charlotte<span class="sep">|</span>Houston<span class="sep">|</span>San Antonio</p>
  </section>

  <section class="card card-back" aria-label="Card back">
    <svg class="back-shapes" viewBox="0 0 540 309" preserveAspectRatio="none" aria-hidden="true">
      <path d="M0 0 H540 V62 C380 70 180 60 0 96 Z" fill="var(--lime)"/>
      <path d="M0 96 C180 60 380 70 540 62" fill="none" stroke="var(--navy)" stroke-width="4"/>
      <path d="M150 309 C250 230 380 150 540 110 V309 Z" fill="var(--lime)"/>
      <path d="M162 309 C260 236 388 160 540 122 V309 Z" fill="var(--navy)"/>
    </svg>

    <div class="person">
      <div class="person-name">Dana Reyes Holt</div>
      <div class="person-title">Director</div>
    </div>

    <div class="back-name">Kelvor Engineers</div>
    <p class="tagline">Multi-Discipline Engineering</p>

    <ul class="contacts">
      <li>555.014.2200
        <svg viewBox="0 0 10 10"><path d="M2 0h2l1 3-1.5 1a6 6 0 0 0 2.5 2.5L7 5l3 1v2a2 2 0 0 1-2 2A8 8 0 0 1 0 2a2 2 0 0 1 2-2z"/></svg>
      </li>
      <li>555.014.7731
        <svg viewBox="0 0 10 10"><path d="M2.5 0h5a1 1 0 0 1 1 1v8a1 1 0 0 1-1 1h-5a1 1 0 0 1-1-1V1a1 1 0 0 1 1-1zm.5 1.5v6h4v-6z"/></svg>
      </li>
      <li>dholt@kelvorstruct.com
        <svg viewBox="0 0 10 10"><path d="M0 2h10v6H0zm1 1v.3l4 2.4 4-2.4V3z"/></svg>
      </li>
      <li>www.kelvorstruct.com
        <svg viewBox="0 0 10 10"><circle cx="5" cy="5" r="5"/></svg>
      </li>
    </ul>
  </section>

</body>
</html>
```